New Business Card Design Project

Use the flyer uploaded and website www.brightoakbuilders.com for inspiration.
List Our Services on Backside of business cards
Marcus Delling
Harborline Builders Inc.
Licensed General Contractors
858-471-6093

Contact Information for Business Card

Use the flyer uploaded and website www.brightoakbuilders.com for inspiration. List Our Services on Backside of business cards Marcus Delling Harborline Builders Inc. Licensed General Contractors 858-471-6093

```html
<!DOCTYPE html>
<html lang="en">
<head>
<meta charset="utf-8">
<title>Harborline Builders – Business Card</title>
<link href="https://fonts.googleapis.com/css2?family=Montserrat:wght@400;500;700&display=swap" rel="stylesheet">
<style>
  :root {
    --page-bg: #a4a4a4;
    --card-bg: #1e1e1e;
    --ink: #ffffff;
    --ink-soft: #e6e6e6;
    --palm-light: #8a8a8a;
    --palm-dark: #262626;
  }
  * { margin: 0; padding: 0; box-sizing: border-box; }
  html, body { width: 1093px; height: 1200px; overflow: hidden; }
  body {
    background: var(--page-bg);
    font-family: "Montserrat", sans-serif;
    color: var(--ink);
    position: relative;
  }
  .card {
    position: absolute;
    left: 252px;
    width: 590px;
    height: 366px;
    background: var(--card-bg);
    border-radius: 18px;
    overflow: hidden;
  }
  .card--front { top: 225px; }
  .card--back { top: 614px; }

  /* Front */
  .brand-name {
    position: absolute;
    font-weight: 400;
    text-transform: uppercase;
    color: var(--ink);
    white-space: nowrap;
  }
  .card--front .brand-name {
    left: 60px; width: 220px;
    top: 212px;
    text-align: center;
    font-size: 14px;
    letter-spacing: 1px;
  }
  .divider {
    position: absolute;
    left: 280px; top: 120px;
    width: 1px; height: 160px;
    background: var(--ink);
  }
  .contact-block {
    position: absolute;
    left: 294px; top: 118px;
  }
  .person-name { font-size: 21px; font-weight: 700; line-height: 1.2; }
  .person-title { font-size: 12.5px; color: var(--ink-soft); margin-top: 1px; }
  .contact-list { list-style: none; margin-top: 27px; }
  .contact-list li {
    display: flex; align-items: center;
    font-size: 12.8px; height: 24px; color: var(--ink-soft);
  }
  .contact-list svg { width: 13px; height: 13px; margin-right: 11px; fill: var(--ink); }
  .license { font-size: 12.5px; color: var(--ink-soft); margin-top: 5px; }

  /* Back */
  .palm-art {
    position: absolute;
    left: 0; top: 0;
    width: 240px; height: 366px;
    background:
      linear-gradient(90deg, rgba(30,30,30,0) 70%, var(--card-bg) 100%),
      linear-gradient(160deg, var(--palm-light) 0%, #555 30%, var(--palm-dark) 75%, var(--card-bg) 100%);
    opacity: 0.55;
  }
  .card--back .brand-name {
    left: 251px; width: 310px;
    top: 52px;
    text-align: center;
    font-size: 21px;
    letter-spacing: 1px;
  }
  .services { position: absolute; left: 259px; top: 120px; }
  .services-title {
    font-size: 17px; font-weight: 700;
    display: inline-block;
    padding-bottom: 4px;
    border-bottom: 1px solid var(--ink);
  }
  .services-list { list-style: none; margin-top: 8px; }
  .services-list li {
    font-size: 13.3px; line-height: 20px; color: var(--ink-soft);
    padding-left: 15px; position: relative;
  }
  .services-list li::before {
    content: ""; position: absolute; left: 2px; top: 8px;
    width: 4px; height: 4px; border-radius: 50%; background: var(--ink);
  }
</style>
</head>
<body>

<section class="card card--front">
  <div class="brand-name">Harborline Builders</div>
  <div class="divider"></div>
  <div class="contact-block">
    <div class="person-name">Marcus Delling</div>
    <div class="person-title">Managing Director</div>
    <ul class="contact-list">
      <li><svg viewBox="0 0 16 16"><path d="M3 2h3l1 3-2 1.5a9 9 0 0 0 4.5 4.5L11 9l3 1v3a1 1 0 0 1-1 1A12 12 0 0 1 2 3a1 1 0 0 1 1-1z"/></svg>858-471-6093</li>
      <li><svg viewBox="0 0 16 16"><path d="M1 3h14v1.5L8 9 1 4.5z"/><path d="M1 6l7 4.5L15 6v7H1z"/></svg>info@brightoakbuilders.com</li>
      <li><svg viewBox="0 0 16 16"><path d="M8 1a7 7 0 1 0 0 14A7 7 0 0 0 8 1zm0 1.5a5.5 5.5 0 0 1 4.8 2.8H10L8.5 7 10 9v3.3A5.5 5.5 0 0 1 3 6.5L5 8l1 3 1-2-1.5-2 2-1V2.5z"/></svg>www.brightoakbuilders.com</li>
    </ul>
    <div class="license">CSLB Licensed No. #1048276</div>
  </div>
</section>

<section class="card card--back">
  <div class="palm-art" role="img" aria-label="Faint large decorative brand artwork area"></div>
  <div class="brand-name">Harborline Builders</div>
  <div class="services">
    <h2 class="services-title">Our Services</h2>
    <ul class="services-list">
      <li>Remodel: Kitchen &amp; Bath</li>
      <li>Painting: Interior &amp; Exterior</li>
      <li>Flooring: Carpet, Vinyl, Wood</li>
      <li>Window: Door Replacement</li>
      <li>Plumbing: Repair &amp; Upgrades</li>
      <li>Energy Efficienct Upgrades</li>
      <li>Deck &amp; Patio consturction</li>
      <li>Water &amp; Mold Damage</li>
      <li>Garage Renovation</li>
    </ul>
  </div>
</section>

</body>
</html>
```